Harborview Estates Business Card for Apartment Buildings

Create business cards for resident managers who run apartment buildings. The audience is the public who are searching for apartment rentals, and current residents who live at the apartment building. Key design element will be incorporating the company logo, however, the logo cannot dominate. The building name and manager name are more important than the logo. Current business card design leaves little room for copy, so we may need to reduce the size on the current card to allow for more space for copy.

Target Market(s)

Adults 18-65 years of age, who are looking for an apartment rental, plus current residents who live at our apartment buildings.

Industry/Entity Type

Property Management

Contact Information for Business Card

A major design element will be use of the company logo. Important property and manager contact information must be part of the design. The size of the logo will need to be reduced to make room for building and manager contact copy.

Font styles to use
Sans Serif

Colors
3176b5
000000
959595
ffffff

Requirements
Must have
• 1) Incorporate the company logo.
• 2) Use the company colors (dark blue, black/grey, over white).
• 3) FEATURE THE BUILDING NAME
• 4) FEATURE THE MANAGER NAME
• 5) The company name is less important than BUILDING and MANAGER
• 6) Manager contact information
• **SEE ATTACHED CREATIVE BRIEF**
Nice to have
• 1) Back of card logo watermark
• 2) Ability to write notes on back of carfd
Should not have
• Avoid letting the company logo dominate the card, the building name and manager are more important than the company logo.

```html
<!DOCTYPE html>
<html lang="en">
<head>
<meta charset="utf-8">
<title>Harborview Estates – Business Card</title>
<link href="https://fonts.googleapis.com/css2?family=Work+Sans:wght@400;500;600&display=swap" rel="stylesheet">
<style>
  :root {
    --brand-blue: #3176b5;
    --card-black: #1f1f1f;
    --stage: #2a2a2a;
    --text-white: #ffffff;
    --text-grey: #959595;
  }
  * { margin: 0; padding: 0; box-sizing: border-box; }
  html, body { width: 1200px; height: 900px; overflow: hidden; }
  body {
    background: var(--stage);
    font-family: "Work Sans", sans-serif;
    color: var(--text-white);
    position: relative;
  }
  .card {
    position: absolute;
    left: 260px;
    width: 680px;
    height: 388px;
    background: var(--card-black);
    border-bottom: 7px solid var(--brand-blue);
  }
  .card--front { top: 44px; }
  .card--back { top: 466px; }

  .brand {
    display: flex;
    align-items: center;
    gap: 12px;
    font-weight: 600;
    color: var(--brand-blue);
    text-transform: uppercase;
    letter-spacing: 0.04em;
    white-space: nowrap;
  }
  .brand__mark {
    width: 16px; height: 16px;
    background: var(--brand-blue);
    flex: none;
  }
  .card--front .brand {
    position: absolute;
    left: 0; right: 0; top: 150px;
    justify-content: center;
    font-size: 38px;
  }
  .card--front .brand__mark { width: 30px; height: 30px; }
  .website {
    position: absolute;
    left: 0; right: 0; bottom: 34px;
    text-align: center;
    font-size: 17px;
    letter-spacing: 0.14em;
    color: var(--text-white);
  }
  .website__domain { color: var(--brand-blue); }

  .card--back .brand {
    position: absolute;
    left: 36px; top: 162px;
    font-size: 22px;
    gap: 10px;
  }
  .divider {
    position: absolute;
    left: 372px; top: 36px;
    width: 2px; height: 290px;
    background: var(--brand-blue);
  }
  .details {
    position: absolute;
    left: 398px; top: 40px;
    right: 28px;
  }
  .manager-name {
    font-size: 24px;
    font-weight: 500;
    color: var(--brand-blue);
    letter-spacing: 0.05em;
    text-transform: uppercase;
    white-space: nowrap;
  }
  .manager-title { font-size: 16px; letter-spacing: 0.04em; margin-top: 4px; }
  .building-name {
    font-size: 16px;
    font-weight: 500;
    color: var(--brand-blue);
    text-transform: uppercase;
    margin-top: 12px;
    white-space: nowrap;
  }
  .address { font-size: 16px; line-height: 1.35; letter-spacing: 0.03em; }
  .contacts { list-style: none; margin-top: 12px; }
  .contacts li {
    display: flex; align-items: center; gap: 12px;
    font-size: 16px; line-height: 1.65; letter-spacing: 0.02em;
    white-space: nowrap;
  }
  .contacts svg { width: 14px; height: 14px; fill: var(--brand-blue); flex: none; }
  .contacts .icon-globe { fill: none; stroke: var(--brand-blue); stroke-width: 1.4; }
</style>
</head>
<body>
  <section class="card card--front">
    <div class="brand"><span class="brand__mark"></span>Harborview Estates</div>
    <p class="website">www.<span class="website__domain">harborviewest</span>.com</p>
  </section>

  <section class="card card--back">
    <div class="brand"><span class="brand__mark"></span>Harborview Estates</div>
    <div class="divider"></div>
    <div class="details">
      <h1 class="manager-name">Marisol Delgado</h1>
      <p class="manager-title">Resident Manager</p>
      <h2 class="building-name">Cedar Court Apartments</h2>
      <p class="address">2418 Linden Avenue<br>Fairhaven, CA 90210</p>
      <ul class="contacts">
        <li><svg viewBox="0 0 16 16"><path d="M3 1l3 0 1 4-2 1c1 2 2 3 4 4l1-2 4 1 0 3c0 1-1 2-2 2C6 14 2 10 1 3c0-1 1-2 2-2z"/></svg><span>555-210-4830</span></li>
        <li><svg viewBox="0 0 16 16"><rect x="4" y="1" width="8" height="4"/><rect x="1" y="6" width="14" height="6" rx="1"/><rect x="4" y="10" width="8" height="5"/></svg><span>555-210-4831</span></li>
        <li><svg viewBox="0 0 16 16"><path d="M4 0h8a1 1 0 0 1 1 1v14a1 1 0 0 1-1 1H4a1 1 0 0 1-1-1V1a1 1 0 0 1 1-1zm1 2v10h6V2z"/></svg><span>555-384-9172</span></li>
        <li><svg viewBox="0 0 16 16"><path d="M1 3h14v1L8 9 1 4z"/><path d="M1 6l7 5 7-5v7H1z"/></svg><span>marisol@harborviewest.com</span></li>
        <li><svg class="icon-globe" viewBox="0 0 16 16"><circle cx="8" cy="8" r="6.5"/><ellipse cx="8" cy="8" rx="2.8" ry="6.5"/><path d="M1.5 8h13"/></svg><span>www.<span class="website__domain">harborviewest</span>.com</span></li>
      </ul>
    </div>
  </section>
</body>
</html>
```